Bref créative
ZARVEN Skin Care
Bright & Fun-filled
Maribel Dunstan
Owner
none on card
zarvenbodycare@plumtree-mail.com
www.zarvenbodycare-shop.com
Natural Skin Care Solutions

```html
<!DOCTYPE html>
<html lang="en">
<head>
<meta charset="utf-8">
<title>ZARVEN Skin Care – Business Card</title>
<link rel="stylesheet" href="https://fonts.googleapis.com/css2?family=Open+Sans:wght@400;600;700&display=swap">
<style>
  :root {
    --backdrop: #6a2c18;
    --card: #ffffff;
    --logo-grey: #8d8d8f;
    --leaf-green: #4f7d1f;
    --text-dark: #333333;
    --band-light: #c3d93a;
    --band-dark: #5e8a22;
  }
  html, body {
    margin: 0;
    padding: 0;
    width: 1200px;
    height: 965px;
    overflow: hidden;
    background: var(--backdrop);
  }
  .business-card {
    position: absolute;
    left: 240px;
    top: 235px;
    width: 774px;
    height: 445px;
    background: var(--card);
    border-radius: 28px;
    overflow: hidden;
    font-family: "Open Sans", Arial, sans-serif;
  }
  .brand-name {
    position: absolute;
    top: 58px;
    left: 0;
    width: 100%;
    text-align: center;
    margin: 0;
    font-size: 104px;
    font-weight: 600;
    letter-spacing: 2px;
    line-height: 1;
    color: var(--logo-grey);
  }
  .tagline {
    position: absolute;
    top: 180px;
    left: 0;
    width: 100%;
    text-align: center;
    margin: 0;
    font-size: 19px;
    font-weight: 600;
    letter-spacing: 1px;
    color: var(--leaf-green);
  }
  .holder {
    position: absolute;
    right: 454px;
    top: 272px;
    text-align: right;
  }
  .holder-name {
    margin: 0;
    font-size: 24px;
    font-weight: 600;
    color: var(--leaf-green);
    line-height: 1.2;
  }
  .holder-role {
    margin: 2px 0 0;
    font-size: 17px;
    color: var(--text-dark);
  }
  .contact-list {
    position: absolute;
    left: 345px;
    top: 276px;
    margin: 0;
    padding: 0;
    list-style: none;
    font-size: 17px;
    line-height: 28px;
    color: var(--text-dark);
  }
  .contact-label {
    font-weight: 700;
    color: var(--leaf-green);
  }
  .wave {
    position: absolute;
    left: 0;
    bottom: 0;
    width: 774px;
    height: 90px;
  }
</style>
</head>
<body>
  <section class="business-card">
    <h1 class="brand-name">ZARVEN</h1>
    <p class="tagline">Natural Skin Care Solutions</p>

    <div class="holder">
      <p class="holder-name">Maribel Dunstan</p>
      <p class="holder-role">Owner</p>
    </div>

    <ul class="contact-list">
      <li><span class="contact-label">Email :</span> zarvenbodycare@plumtree-mail.com</li>
      <li><span class="contact-label">Web :</span> www.zarvenbodycare-shop.com</li>
    </ul>

    <svg class="wave" viewBox="0 0 774 90" preserveAspectRatio="none" aria-hidden="true">
      <defs>
        <linearGradient id="band-fill" x1="0" y1="0" x2="1" y2="0">
          <stop offset="0" stop-color="var(--band-dark)"/>
          <stop offset="0.45" stop-color="var(--band-light)"/>
          <stop offset="1" stop-color="var(--band-dark)"/>
        </linearGradient>
        <linearGradient id="swoosh-fill" x1="0" y1="0" x2="1" y2="0">
          <stop offset="0" stop-color="#9d9d9f"/>
          <stop offset="0.5" stop-color="#d8d8da"/>
          <stop offset="1" stop-color="#a5a5a7"/>
        </linearGradient>
      </defs>
      <path d="M0,8 C190,-3 450,24 774,3 L774,14 C450,40 200,20 0,32 Z" fill="url(#swoosh-fill)"/>
      <path d="M0,58 C220,28 480,34 774,20 L774,90 L0,90 Z" fill="url(#band-fill)"/>
    </svg>
  </section>
</body>
</html>
```